New Dental Office Needs an Attractive and user friendly Website Designed

I need a website for a new dental office. The Name is Harrowfield Dentistry. I would like a Modern design with a user friendly interface and usability.
I would like a landing page, a page that lists the services we offer: Cosmetic Dentistry, Implants, Dental Hygiene, Emergency Services, Restorations, Dentures
Target Market(s)
Mid to upper class
Industry/Entity Type
Dentistry
Coding
Number of Pages Required
1 page
Requirements
Must have
- Landing page that has a scheduling option, Procedures, operating hours, and contact us info
Nice to have
- Appealing design, Soft comforting colors. Easy to navigate page, Modern and professional.

```html
<!DOCTYPE html>
<html lang="en">
<head>
<meta charset="utf-8">
<title>Harrowfield Dentistry</title>
<link href="https://fonts.googleapis.com/css2?family=Poppins:wght@400;500;600;700&display=swap" rel="stylesheet">
<style>
:root{
  --navy:#1e3a86;
  --navy-dark:#0f1d33;
  --footer:#0d1a2e;
  --teal:#5aafc0;
  --ink:#1c2230;
  --muted:#7a808c;
  --soft:#e9eef6;
  --white:#ffffff;
}
*{box-sizing:border-box;margin:0;padding:0}
html,body{width:1200px;height:4908px;overflow:hidden}
body{font-family:'Poppins',sans-serif;color:var(--ink);background:var(--white);position:relative}
.abs{position:absolute}
section,header,footer{position:absolute;left:0;width:1200px}
.btn{position:absolute;background:var(--teal);color:var(--white);font-size:13px;font-weight:500;border-radius:4px;display:flex;align-items:center;justify-content:center}
.eyebrow{position:absolute;left:0;width:1200px;text-align:center;font-size:13px;line-height:16px;color:var(--navy)}
.title{position:absolute;left:0;width:1200px;text-align:center;font-size:30px;line-height:40px;font-weight:600}
.lede{position:absolute;left:350px;width:500px;text-align:center;font-size:13px;line-height:16px;color:var(--muted)}
.ph{position:absolute}

/* top bar */
.topbar{top:0;height:36px;background:var(--navy);color:var(--white);font-size:12px}
.topbar .soc{position:absolute;top:11px;width:14px;height:14px}
.topbar .info{position:absolute;top:10px;display:flex;gap:8px;align-items:center;line-height:16px}

/* hero */
.hero{top:36px;height:650px}
.hero .photo{left:0;top:0;width:1200px;height:650px;background:linear-gradient(100deg,#5a5450 0%,#8b7a70 35%,#c9b3a4 60%,#6f625c 100%)}
.nav{top:0;height:90px;background:rgba(20,20,25,.35)}
.logo{position:absolute;font-weight:600;color:var(--white)}
.nav .links{position:absolute;top:36px;font-size:13px;line-height:18px;color:var(--white)}
.hero h1{position:absolute;left:160px;top:320px;font-size:50px;line-height:62px;font-weight:600;color:var(--white)}
.hero p{position:absolute;left:160px;top:451px;width:440px;font-size:13px;line-height:17px;color:var(--white)}

/* booking */
.band{top:686px;height:583px;background:var(--navy)}
.booking{position:absolute;left:147px;top:623px;width:906px;height:152px;background:var(--white);border-radius:8px;box-shadow:0 6px 20px rgba(0,0,0,.12)}
.booking h3{position:absolute;left:0;width:906px;top:24px;text-align:center;font-size:19px;font-weight:500}
.field{position:absolute;top:74px;width:204px;height:48px;background:#eef1f5;border-radius:4px;font-size:11px;line-height:13px;padding:9px 0 0 44px;color:var(--ink)}
.field small{display:block;color:var(--muted);font-size:10px}
.field svg{position:absolute;left:14px;top:14px}

/* about */
.about-frame{left:162px;width:438px;height:301px;background:#e3e6ea}
.about-person{left:252px;width:260px;height:459px;background:linear-gradient(180deg,#d9c8bc 0%,#eef1f4 30%,#f4f6f8 100%);border-radius:120px 120px 0 0}
.about-copy{position:absolute;left:674px;color:var(--white)}

/* services */
.card{position:absolute;width:276px;height:120px;border-radius:4px;overflow:hidden;background:linear-gradient(160deg,#9fb6cf,#46607e)}
.card span{position:absolute;left:13px;bottom:16px;font-size:15px;line-height:20px;font-weight:600;color:var(--white)}
.card i{position:absolute;right:14px;bottom:12px;width:28px;height:28px;border-radius:50%;background:var(--white);display:flex;align-items:center;justify-content:center}

/* before after */
.magic{top:1825px;height:375px;background:var(--navy-dark)}
.smile{left:162px;top:2038px;width:876px;height:317px;border-radius:10px;overflow:hidden;display:flex}
.smile .l{width:438px;background:linear-gradient(180deg,#7a2a30,#e6d3a8 50%,#7a2a30)}
.smile .r{width:438px;background:linear-gradient(180deg,#7a2a30,#f4f1ea 50%,#7a2a30)}

/* team */
.member{position:absolute;top:2564px;width:168px;text-align:center}
.member .face{width:168px;height:168px;border-radius:50%;background:linear-gradient(160deg,#c8d8e8,#7fa2c6)}
.member b{display:block;margin-top:18px;font-size:14px;line-height:18px;font-weight:500}
.member small{font-size:11px;color:var(--muted)}

/* testimonials */
.testi{top:2924px;height:526px;background:var(--soft)}
.quote{position:absolute;top:3141px;height:179px;background:var(--white);border-radius:4px;box-shadow:0 6px 18px rgba(30,58,134,.08)}
.quote .avatar{position:absolute;left:32px;top:32px;width:58px;height:56px;background:#c9ced6;border-radius:3px}
.quote .who{position:absolute;left:102px;top:42px;font-size:13px;line-height:20px}
.quote p{position:absolute;left:32px;top:112px;right:28px;font-size:12px;line-height:20px;color:var(--muted)}

/* contact */
.contact{top:3450px;height:467px;background:var(--navy);color:var(--white)}
.inp{position:absolute;font-size:11px;line-height:14px;border-bottom:1px solid rgba(255,255,255,.25);padding-bottom:12px}

/* blog */
.post{position:absolute;top:4126px;width:417px;height:322px;background:#f3f4f6;border-radius:4px;overflow:hidden}
.post .img{position:absolute;right:0;top:0;width:143px;height:322px;background:linear-gradient(170deg,#e0c9bc,#6f7fa3)}
.post .tag{position:absolute;left:23px;top:42px;font-size:11px;color:var(--teal)}
.post .date{position:absolute;left:23px;top:60px;font-size:10px;color:var(--muted)}
.post h4{position:absolute;left:23px;top:110px;width:240px;font-size:16px;line-height:24px;font-weight:500}
.post p{position:absolute;left:23px;top:168px;width:235px;font-size:11px;line-height:19px;color:var(--muted)}
.post a{position:absolute;left:23px;top:264px;font-size:11px;color:var(--navy);text-decoration:none;border-bottom:1px solid var(--navy)}

/* footer */
.footer{top:4595px;height:313px;background:var(--footer);color:var(--white)}
.footer h5{position:absolute;font-size:16px;line-height:20px;font-weight:500}
.footer ul{position:absolute;list-style:none;font-size:11px;line-height:27px}
.footer .hours li{display:flex;justify-content:space-between;width:160px}
.footer .c{position:absolute;left:880px;display:flex;align-items:center;gap:10px;font-size:11px}
.footer .c i{width:26px;height:26px;border-radius:50%;background:var(--teal);display:flex;align-items:center;justify-content:center;flex:none}
</style>
</head>
<body>

<header class="topbar">
  <svg class="soc" style="left:157px" viewBox="0 0 14 14"><rect x="1" y="1" width="12" height="12" rx="2" fill="none" stroke="#fff"/></svg>
  <svg class="soc" style="left:195px" viewBox="0 0 14 14"><circle cx="7" cy="7" r="6" fill="none" stroke="#fff"/></svg>
  <svg class="soc" style="left:235px" viewBox="0 0 14 14"><rect x="1" y="1" width="12" height="12" rx="2" fill="none" stroke="#fff"/></svg>
  <svg class="soc" style="left:273px" viewBox="0 0 14 14"><circle cx="7" cy="7" r="6" fill="none" stroke="#fff"/></svg>
  <div class="info" style="left:683px"><svg width="12" height="12" viewBox="0 0 12 12"><path d="M2 1l3 0 1 3-2 1a7 7 0 0 0 3 3l1-2 3 1v3c-6 0-9-3-9-9z" fill="#fff"/></svg>+1 555 010 2040</div>
  <div class="info" style="left:826px"><svg width="13" height="10" viewBox="0 0 13 10"><rect width="13" height="10" rx="1" fill="#fff"/><path d="M0 1l6.5 5L13 1" stroke="#1e3a86" fill="none"/></svg>info@harrowfielddental.com</div>
</header>

<section class="hero">
  <div class="ph photo" role="img" aria-label="Smiling patient in a dental chair during a check-up"></div>
  <div class="abs nav" style="left:0;width:1200px">
    <div class="logo" style="left:160px;top:22px;font-size:21px;line-height:24px">Harrowfield<br><span style="font-size:12px;letter-spacing:4px">DENTISTRY</span></div>
    <div class="links" style="left:434px">Home</div>
    <div class="links" style="left:511px">About Us</div>
    <div class="links" style="left:606px">Services</div>
    <div class="links" style="left:695px">Dentists</div>
    <div class="links" style="left:777px">Contact Us</div>
    <div class="btn" style="left:876px;top:27px;width:162px;height:36px">Book Appointment</div>
  </div>
  <h1>High Quality and<br>Painless Dentistry</h1>
  <p>If you are in need of high-quality, professional and friendly dental care, look no further than our clinic.</p>
  <div class="btn" style="left:160px;top:509px;width:162px;height:40px">Learn More</div>
</section>

<section class="band">
  <div class="ph about-frame" style="top:282px" role="img" aria-label="Clinic interior background"></div>
  <div class="ph about-person" style="top:124px" role="img" aria-label="Dentist in white coat with stethoscope"></div>
  <div class="about-copy" style="top:180px;font-size:13px;line-height:16px">About Us</div>
  <div class="about-copy" style="top:207px;font-size:30px;line-height:37px;font-weight:600;width:400px">Professionals and Personalized Dental Excellence</div>
  <div class="about-copy" style="top:330px;width:370px;font-size:12px;line-height:20px">Welcome to our BrightPath team dedicated to empowering pet owners with valuable knowledge and resources.</div>
  <div class="about-copy" style="top:400px;width:370px;font-size:12px;line-height:20px">Welcome to our BrightPath team dedicated to empowering pet owners with valuable knowledge and resources.</div>
  <div class="btn" style="left:674px;top:486px;width:162px;height:40px">Learn More</div>
</section>

<div class="booking">
  <h3>Book Appointment</h3>
  <div class="field" style="left:27px"><svg width="12" height="16" viewBox="0 0 12 16"><path d="M6 0a6 6 0 0 1 6 6c0 4-6 10-6 10S0 10 0 6a6 6 0 0 1 6-6z" fill="#1e3a86"/><circle cx="6" cy="6" r="2" fill="#fff"/></svg><small>Location</small>Los Angeles, CA</div>
  <div class="field" style="left:243px"><svg width="18" height="16" viewBox="0 0 18 16"><rect y="2" width="18" height="14" rx="1" fill="#1e3a86"/></svg><small>Appointment Date</small>10-05-2025</div>
  <div class="field" style="left:459px"><svg width="20" height="16" viewBox="0 0 20 16"><circle cx="7" cy="5" r="4" fill="#1e3a86"/><circle cx="14" cy="6" r="3" fill="#1e3a86"/><path d="M0 16a7 6 0 0 1 14 0zM12 16a5 5 0 0 1 8 0z" fill="#1e3a86"/></svg><small>Treatment For</small>1 Adult</div>
  <div class="btn" style="left:675px;top:74px;width:206px;height:48px;font-size:12px">BOOK APPOINTMENT</div>
</div>

<section style="top:1269px;height:556px">
  <div class="eyebrow" style="top:59px">Our Services</div>
  <div class="title" style="top:83px">Complete Care for Every Smile</div>
  <div class="lede" style="top:133px">Welcome to our BrightPath team dedicated to empowering pet owners with valuable knowledge and resources.</div>
</section>
<div class="card" style="left:162px;top:1452px" role="img" aria-label="Patient smiling during cosmetic treatment"><span>Cosmetic Dentistry</span><i><svg width="10" height="10" viewBox="0 0 10 10"><path d="M2 8L8 2M3 2h5v5" stroke="#1e3a86" fill="none"/></svg></i></div>
<div class="card" style="left:462px;top:1452px" role="img" aria-label="Dentist examining a patient for implants"><span>Implants</span><i><svg width="10" height="10" viewBox="0 0 10 10"><path d="M2 8L8 2M3 2h5v5" stroke="#1e3a86" fill="none"/></svg></i></div>
<div class="card" style="left:762px;top:1452px" role="img" aria-label="Hygienist cleaning a patient's teeth"><span>Dental Hygiene</span><i><svg width="10" height="10" viewBox="0 0 10 10"><path d="M2 8L8 2M3 2h5v5" stroke="#1e3a86" fill="none"/></svg></i></div>
<div class="card" style="left:162px;top:1588px" role="img" aria-label="Dentist attending an urgent patient visit"><span>Emergency Services</span><i><svg width="10" height="10" viewBox="0 0 10 10"><path d="M2 8L8 2M3 2h5v5" stroke="#1e3a86" fill="none"/></svg></i></div>
<div class="card" style="left:462px;top:1588px" role="img" aria-label="Dentist restoring a patient's tooth"><span>Restorations</span><i><svg width="10" height="10" viewBox="0 0 10 10"><path d="M2 8L8 2M3 2h5v5" stroke="#1e3a86" fill="none"/></svg></i></div>
<div class="card" style="left:762px;top:1588px" role="img" aria-label="Patient being fitted for dentures"><span>Dentures</span><i><svg width="10" height="10" viewBox="0 0 10 10"><path d="M2 8L8 2M3 2h5v5" stroke="#1e3a86" fill="none"/></svg></i></div>
<div class="btn" style="left:520px;top:1742px;width:160px;height:40px">View All Services</div>

<section class="magic" role="img" aria-label="Dark blue backdrop with a softly lit smiling face">
  <div class="eyebrow" style="top:59px;color:var(--white)">Before And After</div>
  <div class="title" style="top:85px;color:var(--white)">Witness The Magic</div>
  <div class="lede" style="top:134px;color:#cfd5e0">Welcome to our BrightPath team dedicated to empowering pet owners with valuable knowledge and resources.</div>
</section>
<div class="ph smile" role="img" aria-label="Close-up smile comparing teeth before and after whitening"><div class="l"></div><div class="r"></div></div>
<div class="abs" style="left:599px;top:2038px;width:2px;height:317px;background:#fff"></div>
<div class="abs" style="left:578px;top:2179px;width:44px;height:44px;border-radius:50%;background:#fff;font-size:9px;font-weight:600;display:flex;align-items:center;justify-content:center">DRAG</div>
<div class="abs" style="left:172px;top:2310px;font-size:8px;color:#fff;transform:rotate(-90deg)">BEFORE</div>
<div class="abs" style="left:1005px;top:2310px;font-size:8px;color:#fff;transform:rotate(90deg)">AFTER</div>

<section style="top:2355px;height:569px">
  <div class="eyebrow" style="top:58px">Meet Our Dental Team</div>
  <div class="title" style="top:82px">Committed to Your Smile</div>
  <div class="lede" style="top:133px">Welcome to our BrightPath team dedicated to empowering pet owners with valuable knowledge and resources.</div>
</section>
<div class="member" style="left:175px"><div class="face" role="img" aria-label="Portrait of a female dentist"></div><b>Dr. Claire Morgan</b><small>Lead Dentist</small></div>
<div class="member" style="left:402px"><div class="face" role="img" aria-label="Portrait of a male dentist"></div><b>Dr. Claire Morgan</b><small>Lead Dentist</small></div>
<div class="member" style="left:628px"><div class="face" role="img" aria-label="Portrait of a female dentist"></div><b>Dr. Claire Morgan</b><small>Lead Dentist</small></div>
<div class="member" style="left:855px"><div class="face" role="img" aria-label="Portrait of a male dentist"></div><b>Dr. Claire Morgan</b><small>Lead Dentist</small></div>
<div class="btn" style="left:520px;top:2821px;width:160px;height:40px">View All Team</div>

<section class="testi">
  <div class="eyebrow" style="top:57px">Our Testimonial</div>
  <div class="title" style="top:81px">Pleasing Patients Is Our Greatest Achievement</div>
  <div class="lede" style="top:133px">Welcome to our BrightPath team dedicated to empowering pet owners with valuable knowledge and resources.</div>
</section>
<div class="quote" style="left:200px;width:385px"><div class="avatar" role="img" aria-label="Patient photo"></div><div class="who">Mara Ellison<br><b style="font-weight:500">Northvale Studio Ltd.</b></div><svg class="abs" style="right:32px;top:40px" width="38" height="30" viewBox="0 0 38 30"><path d="M0 30V16C0 6 6 1 14 0v6c-4 1-6 4-6 8h7v16zM22 30V16c0-10 6-15 14-16v6c-4 1-6 4-6 8h7v16z" fill="#a9d3dc"/></svg><p>It was pleasure to work with Harrowfield. it's helped us in our contributed his technical expertise.</p></div>
<div class="quote" style="left:617px;width:385px"><div class="avatar" role="img" aria-label="Patient photo"></div><div class="who">Mara Ellison<br><b style="font-weight:500">Northvale Studio Ltd.</b></div><svg class="abs" style="right:32px;top:40px" width="38" height="30" viewBox="0 0 38 30"><path d="M0 30V16C0 6 6 1 14 0v6c-4 1-6 4-6 8h7v16zM22 30V16c0-10 6-15 14-16v6c-4 1-6 4-6 8h7v16z" fill="#a9d3dc"/></svg><p>It was pleasure to work with Harrowfield. it's helped us in our contributed his technical expertise.</p></div>
<div class="btn" style="left:512px;top:3368px;width:176px;height:40px">View All Testimonial</div>

<section class="contact">
  <div class="ph" style="left:678px;top:59px;width:522px;height:351px;border-radius:175px 0 0 175px;background:linear-gradient(120deg,#c9b6aa,#8fa3bf 70%,#3d5a86)" role="img" aria-label="Patient smiling while dentist works with instruments"></div>
  <div class="abs" style="left:183px;top:53px;font-size:13px;line-height:16px">Contact</div>
  <div class="abs" style="left:183px;top:72px;font-size:26px;line-height:34px;font-weight:600">Make An Appointment</div>
  <div class="inp" style="left:183px;top:141px;width:175px">Name*</div>
  <div class="inp" style="left:400px;top:141px;width:175px">Company Name</div>
  <div class="inp" style="left:183px;top:202px;width:175px">Phone</div>
  <div class="inp" style="left:400px;top:202px;width:175px">Email Address*</div>
  <div class="inp" style="left:183px;top:264px;width:392px;height:71px">Your Message</div>
  <div class="btn" style="left:181px;top:377px;width:206px;height:40px;font-size:12px">SUBMIT</div>
</section>

<section style="top:3917px;height:678px">
  <div class="eyebrow" style="top:58px">Our Latest Blog</div>
  <div class="title" style="top:83px">Latest Posts &amp; Articles</div>
  <div class="lede" style="top:133px">Welcome to our BrightPath team dedicated to empowering pet owners with valuable knowledge and resources.</div>
</section>
<div class="post" style="left:162px"><div class="img" role="img" aria-label="Patient receiving dental care"></div><div class="tag">HARROWFIELD</div><div class="date">Mar 25, 2025</div><h4>How to Choose the Best In-Home Pet Care Service</h4><p>Consectetuer fringilla aenean sagittis potenti ullamcorper nam porta feugiat. Ante urna congue feugiat efficitur vel duis.</p><a>LEARN MORE &rsaquo;</a></div>
<div class="post" style="left:619px"><div class="img" role="img" aria-label="Dentist treating a patient"></div><div class="tag">HARROWFIELD</div><div class="date">Mar 25, 2025</div><h4>How to Choose the Best In-Home Pet Care Service</h4><p>Consectetuer fringilla aenean sagittis potenti ullamcorper nam porta feugiat. Ante urna congue feugiat efficitur vel duis.</p><a>LEARN MORE &rsaquo;</a></div>
<div class="btn" style="left:520px;top:4494px;width:160px;height:40px;font-size:12px">VIEW ALL BLOG</div>

<footer class="footer">
  <div class="logo" style="left:160px;top:70px;font-size:22px;line-height:24px">Harrowfield<br><span style="font-size:12px;letter-spacing:4px">DENTISTRY</span></div>
  <div class="abs" style="left:160px;top:128px;width:280px;font-size:11px;line-height:17px">It is a long established fact that a reader will be distracted by the readable content of a page when looking at its layout.</div>
  <svg class="abs" style="left:160px;top:202px" width="14" height="14"><rect x="1" y="1" width="12" height="12" rx="2" fill="none" stroke="#5aafc0"/></svg>
  <svg class="abs" style="left:202px;top:202px" width="14" height="14"><circle cx="7" cy="7" r="6" fill="none" stroke="#5aafc0"/></svg>
  <svg class="abs" style="left:244px;top:202px" width="14" height="14"><rect x="1" y="1" width="12" height="12" rx="2" fill="none" stroke="#5aafc0"/></svg>
  <h5 style="left:490px;top:54px">Quick Links</h5>
  <ul style="left:490px;top:92px"><li>Home</li><li>About Us</li><li>Services</li><li>Team</li><li>Contact Us</li></ul>
  <h5 style="left:660px;top:54px">Opening Hours</h5>
  <ul class="hours" style="left:660px;top:92px"><li><span>Mon – Fri</span><span>8:00 – 18:00</span></li><li><span>Saturday</span><span>9:00 – 14:00</span></li><li><span>Sunday</span><span>Closed</span></li><li><span>Emergency</span><span>24 / 7</span></li></ul>
  <h5 style="left:880px;top:54px">Contact Us</h5>
  <div class="c" style="top:98px"><i><svg width="11" height="11" viewBox="0 0 12 12"><path d="M2 1l3 0 1 3-2 1a7 7 0 0 0 3 3l1-2 3 1v3c-6 0-9-3-9-9z" fill="#fff"/></svg></i>+1 555 010 2040</div>
  <div class="c" style="top:137px"><i><svg width="12" height="9" viewBox="0 0 13 10"><rect width="13" height="10" rx="1" fill="#fff"/><path d="M0 1l6.5 5L13 1" stroke="#5aafc0" fill="none"/></svg></i>hello@harrowfielddental.com</div>
  <div class="c" style="top:176px"><i><svg width="9" height="12" viewBox="0 0 12 16"><path d="M6 0a6 6 0 0 1 6 6c0 4-6 10-6 10S0 10 0 6a6 6 0 0 1 6-6z" fill="#fff"/></svg></i>122, Lorem ipsum dolird</div>
  <div class="abs" style="left:160px;top:257px;width:880px;height:1px;background:rgba(255,255,255,.15)"></div>
  <div class="abs" style="left:0;width:1200px;top:276px;text-align:center;font-size:11px">Copyright © 2025 Harrowfield. All rights reserved.</div>
</footer>

</body>
</html>
```